Crypto currency project website revamp

Our current website is: http://www.kobaltchain.org

The new logo is also attached.

Here are some examples of the other crypto websites. Our goal is to re-make the above website to look and feel like the followings:

1) https://zyvanlabs.com/

2) https://tavo.io/

3) https://paylume.network/#/

Please submit your designs. Once we found the right design we need to interate a bit and add 3 or 4 more sections to it.

The coded website needs to be responsive

```html
<!DOCTYPE html>
<html lang="en">
<head>
<meta charset="utf-8">
<title>Kobalt Network</title>
<link rel="stylesheet" href="https://fonts.googleapis.com/css2?family=Montserrat:wght@400;500;600;700&display=swap">
<style>
:root{
  --navy:#150c36;
  --indigo:#27187a;
  --ink:#333340;
  --muted:#6b6b78;
  --blue:#1a7cf5;
  --cyan:#19b8f0;
  --glow:#2fd6f6;
  --gold:#f0b636;
  --pale:#e5f1f4;
  --pale-blue:#d8e8f4;
  --line:#e2e2e8;
  --tick:#2a8de0;
  --white:#ffffff;
}
*{margin:0;padding:0;box-sizing:border-box}
html,body{width:1200px;height:3622px;overflow:hidden;background:var(--white)}
body{position:relative;font-family:"Montserrat",sans-serif;color:var(--ink)}
.abs{position:absolute}
.btn{position:absolute;display:flex;align-items:center;justify-content:center;border-radius:20px;color:var(--white);font-size:14px;font-weight:500;background:linear-gradient(90deg,var(--blue),var(--cyan))}
.section-title{position:absolute;left:0;width:1200px;text-align:center;color:var(--indigo);font-weight:500;font-size:36px}
p.body-text{font-size:13.5px;line-height:23.5px;color:var(--muted)}
/* hero */
.hero-shape{left:0;top:0}
.logo{left:87px;top:26px;display:flex;align-items:center;gap:10px;font-weight:700;font-size:17px;color:var(--navy)}
.logo-dot{width:44px;height:44px;border-radius:50%;background:var(--navy)}
.nav{top:40px;left:588px;display:flex;gap:41px;font-size:12px;font-weight:500;color:var(--white)}
.hero-title{left:82px;top:226px;font-size:92px;line-height:100px;font-weight:600;color:var(--indigo);letter-spacing:2px}
.hero-sub{left:87px;top:322px;font-size:32px;line-height:42px;font-weight:500;color:var(--navy)}
.hero-art{left:690px;top:90px;width:480px;height:480px;border-radius:50%;
  background:radial-gradient(closest-side,rgba(47,214,246,.95),rgba(28,150,230,.75) 45%,rgba(40,70,180,.35) 75%,rgba(21,12,54,0) 100%)}
.hero-art-core{left:800px;top:190px;width:280px;height:280px;border-radius:50%;
  background:radial-gradient(closest-side,rgba(150,240,255,.9),rgba(47,214,246,0))}
/* steps */
.step{position:absolute;top:804px;width:320px;text-align:center}
.step-icon{margin:0 auto;width:170px;height:140px;position:relative}
.step-num{position:absolute;left:0;top:18px;font-size:110px;font-weight:400;line-height:100px;color:transparent;-webkit-text-stroke:2px #3f7ede}
.step-circle{position:absolute;right:0;top:0;width:140px;height:140px;border-radius:50%;border:2px solid #5fb8f0;background:var(--white)}
.step-art{position:absolute;left:28px;top:28px;width:82px;height:82px;border-radius:50%;background:radial-gradient(circle at 40% 40%,#fbd56b,var(--gold) 45%,rgba(240,182,54,.25) 75%,rgba(255,255,255,0))}
.step-art.blue{background:radial-gradient(circle at 55% 55%,#3b8fe8,#1d5cc0 45%,rgba(240,182,54,.35) 70%,rgba(255,255,255,0))}
.step-text{margin-top:22px;font-size:17px;line-height:26px;font-weight:500;color:var(--ink)}
/* bands */
.band{position:absolute;left:0;width:1200px}
.split-title{font-size:36px;font-weight:600;color:var(--indigo);line-height:48px}
.check-list{list-style:none;font-size:14.5px;color:var(--muted)}
.check-list li{display:flex;align-items:center;gap:12px;height:26.5px}
/* team */
.member{position:absolute;top:2841px;width:300px;text-align:center}
.member-photo{margin:0 auto;width:234px;height:234px;border-radius:50%;
  background:linear-gradient(180deg,#d9d6d2 0%,#b8a89a 45%,#8a7d72 65%,#2e2e34 100%)}
.member-name{margin-top:30px;font-size:25px;font-weight:600;color:#20202a}
.member-role{margin-top:6px;font-size:13px;color:#3a3a48}
/* footer */
.foot-head{font-size:19px;font-weight:600;color:#2b2b38}
.foot-links{list-style:none;font-size:12.5px;font-weight:500;color:#2b2b38;letter-spacing:.5px}
.foot-links li{height:26.5px}
.social{display:flex;gap:10px}
.social span{width:38px;height:38px;border-radius:50%}
</style>
</head>
<body>

<!-- hero -->
<svg class="abs hero-shape" width="1200" height="602" viewBox="0 0 1200 602">
  <defs>
    <linearGradient id="edge" x1="0" y1="0" x2="0" y2="1">
      <stop offset="0" stop-color="#3f78d8"/><stop offset="1" stop-color="#5b2fa0"/>
    </linearGradient>
  </defs>
  <path d="M480 0 C560 80 640 160 600 260 C560 360 470 420 500 602 L1200 602 L1200 0 Z" fill="url(#edge)"/>
  <path d="M540 0 C620 90 700 170 660 270 C620 370 560 430 580 602 L1200 602 L1200 0 Z" fill="var(--navy)"/>
</svg>
<div class="abs logo"><span class="logo-dot"></span>Kobalt network</div>
<nav class="abs nav"><span>HOME</span><span>WHAT IS KOBALT</span><span>CODEVAULT</span><span>YELLOW PAPER</span><span>CONTACT</span></nav>
<div class="abs hero-art" role="img" aria-label="Isometric illustration of a glowing laptop with stacked coins"></div>
<div class="abs hero-art-core" aria-hidden="true"></div>
<h1 class="abs hero-title">KOBALT</h1>
<div class="abs hero-sub">Future of cryptocurrencies<br>we were promised.</div>
<div class="btn" style="left:87px;top:430px;width:173px;height:36px">Get Started Now</div>

<!-- how it works -->
<h2 class="section-title" style="top:696px">HERE'S HOW IT WORKS:</h2>
<div class="step" style="left:94px"><div class="step-icon"><span class="step-num">1</span><span class="step-circle"><span class="step-art" role="img" aria-label="Stack of coins illustration"></span></span></div><div class="step-text">Hello!<br>Let me take you to the<br>Kobalt journey</div></div>
<div class="step" style="left:424px"><div class="step-icon"><span class="step-num">2</span><span class="step-circle"><span class="step-art" role="img" aria-label="Thumbs up with coins illustration"></span></span></div><div class="step-text">We were promised<br>a future... and we are going<br>to MAKE it happen</div></div>
<div class="step" style="left:756px"><div class="step-icon"><span class="step-num">3</span><span class="step-circle"><span class="step-art blue" role="img" aria-label="Exchange of two coins illustration"></span></span></div><div class="step-text">Kobalt<br>is a decentralized network<br>and exchange</div></div>

<!-- what is -->
<div class="band" style="top:1142px;height:483px;background:var(--pale)"></div>
<svg class="abs" style="left:58px;top:1178px" width="456" height="416" viewBox="0 0 456 416">
  <defs>
    <linearGradient id="blobA" x1="0" y1="0" x2="1" y2="1"><stop offset="0" stop-color="#1d5f86"/><stop offset="1" stop-color="#1c1450"/></linearGradient>
    <radialGradient id="glowA" cx="0.45" cy="0.45" r="0.6"><stop offset="0" stop-color="#6fe3fb"/><stop offset="0.35" stop-color="#22a8e8"/><stop offset="0.7" stop-color="#1d3f9a"/><stop offset="1" stop-color="#12164a"/></radialGradient>
  </defs>
  <path d="M40 80 C110 0 330 -10 420 50 C480 100 440 220 400 300 C350 400 240 430 150 390 C60 350 -30 160 40 80 Z" fill="url(#blobA)"/>
  <path d="M70 100 C140 30 320 20 395 70 C445 110 410 220 375 290 C330 375 240 395 160 365 C80 335 10 170 70 100 Z" fill="url(#glowA)" role="img" aria-label="Isometric illustration of servers and data blocks"/>
</svg>
<h2 class="abs split-title" style="left:594px;top:1248px;font-size:33px">WHAT IS KOBALT?</h2>
<p class="abs body-text" style="left:594px;top:1302px;width:520px">Kobalt is a peer-to-peer graph to exchange and transact most crypto-currencies with NO fee or counterparty risk. Kobalt is a decentralized, and distributed ledger technology with built-in support to read across chains. This means Kobalt is able to represent almost any crypto-currency and allow them to be exchanged and transacted in the Kobalt network. Valucoin is expensive and slow to trade, in Kobalt network Valucoin can be traded or exchanged fast, and without any fees.</p>
<div class="btn" style="left:594px;top:1476px;width:128px;height:36px">Read More</div>

<!-- internet of value -->
<h2 class="abs split-title" style="left:87px;top:1758px">INTERNET<br>of VALUE is here!</h2>
<p class="abs body-text" style="left:87px;top:1858px;width:520px">Kobalt is a peer-to-peer graph to exchange and transact most crypto-currencies with NO fee or counterparty risk. Kobalt is a decentralized, and distributed ledger technology with built-in support to read across chains. This means Kobalt is able to represent almost any crypto-currency and allow them to be exchanged and transacted in the Kobalt network. Valucoin is expensive and slow to trade, in Kobalt network Valucoin can be traded or exchanged fast, and without any fees.</p>
<div class="btn" style="left:87px;top:2032px;width:130px;height:36px">Read More</div>
<svg class="abs" style="left:652px;top:1709px" width="460" height="416" viewBox="0 0 460 416">
  <defs>
    <linearGradient id="blobB" x1="0" y1="0" x2="1" y2="1"><stop offset="0" stop-color="#1e6a94"/><stop offset="1" stop-color="#22175a"/></linearGradient>
    <radialGradient id="coins" cx="0.5" cy="0.5" r="0.5"><stop offset="0" stop-color="#f7c64a"/><stop offset="0.45" stop-color="#e8962a"/><stop offset="0.75" stop-color="#f3d6a8"/><stop offset="1" stop-color="#ffffff"/></radialGradient>
  </defs>
  <path d="M60 90 C140 10 340 -20 420 40 C480 90 450 230 410 310 C360 410 220 430 130 380 C40 330 -20 170 60 90 Z" fill="url(#blobB)"/>
  <path d="M78 104 C150 30 335 5 405 55 C460 95 430 225 392 300 C345 392 220 408 140 362 C60 318 10 175 78 104 Z" fill="var(--white)"/>
  <ellipse cx="256" cy="227" rx="140" ry="70" fill="url(#coins)" role="img" aria-label="Illustration of three gold coins"/>
</svg>

<!-- centralized vs decentralized -->
<div class="band" style="top:2204px;height:400px;background:var(--pale)"></div>
<h2 class="section-title" style="top:2274px">Centralized versus Decentralized</h2>
<svg class="abs" style="left:133px;top:2366px" width="170" height="157" viewBox="0 0 170 157">
  <defs><radialGradient id="glowC" cx="0.5" cy="0.5" r="0.55"><stop offset="0" stop-color="#5fd8f8"/><stop offset="0.45" stop-color="#2285d8"/><stop offset="1" stop-color="#13214f"/></radialGradient></defs>
  <path d="M20 35 C60 -5 150 0 165 40 C178 80 150 140 100 152 C50 162 -10 80 20 35 Z" fill="url(#glowC)" role="img" aria-label="Illustration of a central server stack"/>
</svg>
<ul class="abs check-list" style="left:338px;top:2406px">
  <li><svg width="14" height="14" viewBox="0 0 14 14"><circle cx="7" cy="7" r="7" fill="var(--tick)"/><path d="M3.8 7.2l2.2 2.2 4.2-4.4" stroke="#fff" stroke-width="1.6" fill="none"/></svg>Exchange controls the funds</li>
  <li><svg width="14" height="14" viewBox="0 0 14 14"><circle cx="7" cy="7" r="7" fill="var(--tick)"/><path d="M3.8 7.2l2.2 2.2 4.2-4.4" stroke="#fff" stroke-width="1.6" fill="none"/></svg>Prone to hack</li>
  <li><svg width="14" height="14" viewBox="0 0 14 14"><circle cx="7" cy="7" r="7" fill="var(--tick)"/><path d="M3.8 7.2l2.2 2.2 4.2-4.4" stroke="#fff" stroke-width="1.6" fill="none"/></svg>Tooling limited by exchange</li>
</ul>
<svg class="abs" style="left:616px;top:2366px" width="170" height="157" viewBox="0 0 170 157">
  <defs><radialGradient id="glowD" cx="0.5" cy="0.55" r="0.55"><stop offset="0" stop-color="#c45ae8"/><stop offset="0.45" stop-color="#3d62e0"/><stop offset="1" stop-color="#1a1650"/></radialGradient></defs>
  <path d="M20 35 C60 -5 150 0 165 40 C178 80 150 140 100 152 C50 162 -10 80 20 35 Z" fill="url(#glowD)" role="img" aria-label="Illustration of a distributed network of nodes"/>
</svg>
<ul class="abs check-list" style="left:826px;top:2406px">
  <li><svg width="14" height="14" viewBox="0 0 14 14"><circle cx="7" cy="7" r="7" fill="var(--tick)"/><path d="M3.8 7.2l2.2 2.2 4.2-4.4" stroke="#fff" stroke-width="1.6" fill="none"/></svg>Only user controls the funds</li>
  <li><svg width="14" height="14" viewBox="0 0 14 14"><circle cx="7" cy="7" r="7" fill="var(--tick)"/><path d="M3.8 7.2l2.2 2.2 4.2-4.4" stroke="#fff" stroke-width="1.6" fill="none"/></svg>Can NOT be hacked</li>
  <li><svg width="14" height="14" viewBox="0 0 14 14"><circle cx="7" cy="7" r="7" fill="var(--tick)"/><path d="M3.8 7.2l2.2 2.2 4.2-4.4" stroke="#fff" stroke-width="1.6" fill="none"/></svg>Open community tooling</li>
</ul>

<!-- team -->
<svg class="abs" style="left:0;top:2600px" width="1200" height="659" viewBox="0 0 1200 659">
  <rect width="1200" height="659" fill="var(--pale-blue)"/>
  <path d="M0 320 C300 420 700 300 1200 360 L1200 659 L0 659 Z" fill="var(--pale)"/>
</svg>
<h2 class="section-title" style="top:2694px;color:#33333f;font-weight:600">THE BEST TEAM AVAILABLE</h2>
<p class="abs body-text" style="left:260px;top:2752px;width:680px;text-align:center;font-size:12.5px;line-height:26px">Lorem Ipsum is simply dummy text of the printing and typesetting industry. Lorem Ipsum has been the industry's standard dummy text ever since the 1500s</p>
<div class="member" style="left:111px"><div class="member-photo" role="img" aria-label="Portrait photo of Marek D Olsen"></div><div class="member-name">Marek D Olsen</div><div class="member-role">Founder &amp; General Manager</div></div>
<div class="member" style="left:449px"><div class="member-photo" role="img" aria-label="Portrait photo of Samuel R"></div><div class="member-name">Samuel R</div><div class="member-role">Information &amp; Knowledge Manager</div></div>
<div class="member" style="left:787px"><div class="member-photo" role="img" aria-label="Portrait photo of Adrian P Kessler"></div><div class="member-name">Adrian P Kessler</div><div class="member-role">Content Manager</div></div>

<!-- footer -->
<div class="abs foot-head" style="left:87px;top:3320px">Quick Links</div>
<ul class="abs foot-links" style="left:87px;top:3370px">
  <li>&gt;&nbsp; HOME</li><li>&gt;&nbsp; WHAT IS KOBALT</li><li>&gt;&nbsp; CODEVAULT</li><li>&gt;&nbsp; YELLOW PAPER</li><li>&gt;&nbsp; CONTACT</li>
</ul>
<div class="abs foot-head" style="left:338px;top:3320px">About Us</div>
<p class="abs body-text" style="left:338px;top:3350px;width:420px;font-size:12.5px;line-height:26px;color:#555560">Lorem Ipsum is simply dummy text of the printing and typesetting industry. Lorem Ipsum has been the industry's standard dummy text ever since the 1500s, when an unknown printer took a galley of type and scrambled it to make a type specimen book. It has survived not only five centuries.</p>
<div class="abs" style="left:338px;top:3493px;width:172px;height:36px;border:1.5px solid var(--blue);border-radius:20px;display:flex;align-items:center;justify-content:center;font-size:13px;color:var(--blue)">Get Started Now</div>
<div class="abs foot-head" style="left:888px;top:3320px">Stay in Touch</div>
<div class="abs social" style="left:886px;top:3358px" aria-label="Social links">
  <span style="background:#3b5a98"></span><span style="background:#2ea6e0"></span><span style="background:#d84a3a"></span><span style="background:#d42a2a"></span><span style="background:#b52d8f"></span>
</div>
<div class="abs" style="left:879px;top:3424px;font-size:15px;font-weight:600;color:#2b2b38">Register for Articles</div>
<div class="btn" style="left:879px;top:3460px;width:222px;height:46px;border-radius:23px;font-size:16px">Email</div>
<div class="abs" style="left:87px;top:3561px;width:1026px;height:1px;background:var(--line)"></div>
<div class="abs" style="left:0;top:3584px;width:1200px;text-align:center;font-size:13px;color:#555560">Copyright © 2018. Kobalt Network. All rights reserved.</div>

</body>
</html>
```